Label design needed for a new brain focus supplement. Velmarix.com

Hi I’m looking for a quality label design for a my new supplement. The supplement is a nootropic (brain focus booster). I’ll also upload my competitors designs as a reference and to get some ideas.

I was thinking to use a white glossy background with the gold logo in top with some gold graphics added. Along with some focus driven text.

Dimensions for label are 300mm x 105mm Landscape. Please allow a 5mm safe text area.

Target Market(s)

High achieving focus driven People.

Font styles to use
Sans Serif

Colors

Designer to choose colors to be used in the design.

Requirements
Must have
• Good quality design.
Nice to have
• wording to use on label
• EXTREME FOCUS
• Brain food supplement
• High quality
• Premium blend
• Dietary supplement
Should not have
• Bright colourful colours. This is a premium product and label should show this

```html
<!DOCTYPE html>
<html lang="en">
<head>
<meta charset="utf-8">
<title>Velmarix Extreme Focus – Label</title>
<link rel="stylesheet" href="https://fonts.googleapis.com/css2?family=Josefin+Sans:wght@300;400;600;700&family=Montserrat:wght@700&display=swap">
<style>
  :root {
    --page: #f2f2f2;
    --label: #0b0b0b;
    --gold: #d9b25a;
    --gold-soft: #b8913f;
    --gold-deep: #7a5a1e;
    --text-light: #f1ece2;
    --text-copy: #e9e3d6;
  }
  * { margin: 0; padding: 0; box-sizing: border-box; }
  html, body { width: 1200px; height: 1200px; overflow: hidden; }
  body {
    background: var(--page);
    font-family: "Josefin Sans", sans-serif;
    display: flex;
    align-items: center;
    justify-content: center;
  }
  .label {
    width: 1200px;
    height: 420px;
    background: var(--label);
    display: flex;
  }
  .label__front, .label__back { width: 600px; height: 100%; }

  /* Front panel */
  .label__front {
    display: flex;
    flex-direction: column;
    align-items: center;
    padding-top: 26px;
    text-align: center;
  }
  .emblem {
    width: 130px;
    height: 130px;
    border-radius: 50%;
    background: radial-gradient(circle, var(--gold) 0%, var(--gold-soft) 35%, var(--gold-deep) 60%, var(--label) 72%);
  }
  .brand {
    display: flex;
    align-items: center;
    gap: 10px;
    margin-top: 12px;
  }
  .brand__dot {
    width: 22px; height: 22px;
    border-radius: 50%;
    background: var(--gold);
  }
  .brand__name {
    font-family: "Montserrat", sans-serif;
    font-weight: 700;
    font-size: 50px;
    line-height: 1;
    color: var(--gold);
  }
  .headline {
    margin-top: 12px;
    font-weight: 300;
    font-size: 34px;
    letter-spacing: 0.5px;
    color: var(--gold);
  }
  .claims {
    font-weight: 300;
    font-size: 19px;
    line-height: 1.3;
    color: var(--text-light);
  }
  .claims--top { margin-top: 6px; }
  .divider {
    width: 300px;
    height: 1px;
    background: var(--gold-soft);
    margin: 8px 0;
  }
  .count {
    margin-top: 6px;
    font-size: 14px;
    color: var(--gold);
  }

  /* Back panel */
  .label__back {
    display: flex;
    align-items: flex-start;
    padding-top: 64px;
  }
  .benefits {
    width: 250px;
    display: flex;
    flex-direction: column;
    align-items: center;
    gap: 18px;
  }
  .benefit {
    display: flex;
    flex-direction: column;
    align-items: center;
    gap: 8px;
  }
  .benefit__icon {
    width: 56px; height: 64px;
    border-radius: 6px;
    background: linear-gradient(180deg, var(--gold-soft), var(--gold-deep));
    opacity: 0.55;
  }
  .benefit__name {
    font-size: 16px;
    letter-spacing: 0.5px;
    color: var(--gold);
  }
  .info {
    width: 290px;
    font-size: 13.5px;
    line-height: 1.45;
    color: var(--text-copy);
  }
  .info p + p { margin-top: 12px; }
  .info__key { font-weight: 700; color: var(--gold); }
  .info__legal {
    margin-top: 18px;
    font-weight: 600;
    color: var(--gold);
  }
</style>
</head>
<body>
  <main class="label">
    <section class="label__front">
      <div class="emblem" role="img" aria-label="Gold emblem of a flexing brain inside a geometric star frame"></div>
      <div class="brand">
        <span class="brand__dot"></span>
        <span class="brand__name">Velmarix</span>
      </div>
      <h1 class="headline">EXTREME FOCUS</h1>
      <p class="claims claims--top">Brain Food Supplement<br>High Quality</p>
      <div class="divider"></div>
      <p class="claims">Premium Blend<br>Dietary supplement</p>
      <p class="count">90 Capsules</p>
    </section>

    <section class="label__back">
      <div class="benefits">
        <div class="benefit">
          <div class="benefit__icon" role="img" aria-label="Line icon of a head with a target"></div>
          <span class="benefit__name">FOCUS</span>
        </div>
        <div class="benefit">
          <div class="benefit__icon" role="img" aria-label="Line icon of a head with a brain"></div>
          <span class="benefit__name">MEMORY</span>
        </div>
        <div class="benefit">
          <div class="benefit__icon" role="img" aria-label="Line icon of a head with a light bulb"></div>
          <span class="benefit__name">CLARITY</span>
        </div>
      </div>
      <div class="info">
        <p><span class="info__key">INGREDIENTS:</span> Hi I'm looking for a quality label design for a my new supplement. The supplement is a nootropic (brain focus booster). I'll also upload my competitors designs as a reference and to get some ideas. Dimensions for label are 300mm x 105mm Landscape. Please allow a 5mm safe text area.</p>
        <p>Hi I'm looking for a quality label design for a my new supplement. The supplement is a nootropic (brain focus booster). I'll also upload my competitors designs as a reference and to get some ideas.</p>
        <p class="info__legal">Distributed by Halvern Supplements,<br>Ashbridge, AB12 3CD, United Kingdom manufactured in the UK<br>MADE IN UK</p>
      </div>
    </section>
  </main>
</body>
</html>
```